BOLD & MINIMALIST DESIGN NEEDED

We want a very bold but minimalistic business card design that is impactful and utilizes both sides of the business card. Our current logo is included for your use.

We want bold fonts and good use of negative space. We don't want the logo to overpower the design.

Target Market(s)

Professionals who are building new commercial buildings.

Industry/Entity Type

Construction

Contact Information for Business Card

Name, Title, email, office phone, cell phone, website

Font styles to use
Serif
Sans Serif

Requirements
Must have
• Bold design!

```html
<!DOCTYPE html>
<html lang="en">
<head>
<meta charset="utf-8">
<title>Ridgeway Design + Build — Business Card</title>
<link rel="stylesheet" href="https://fonts.googleapis.com/css2?family=Montserrat:wght@400;500;800&display=swap">
<style>
  :root {
    --backdrop: #2b2b2b;
    --card-black: #111111;
    --card-white: #ffffff;
    --brand-green: #7cc242;
    --text-light: #f2f2f2;
    --text-dark: #111111;
    --text-muted: #333333;
  }
  * { box-sizing: border-box; margin: 0; padding: 0; }
  html, body {
    width: 1200px; height: 874px; overflow: hidden;
    background: var(--backdrop);
    font-family: "Montserrat", Arial, sans-serif;
  }
  .canvas {
    position: relative; width: 1200px; height: 874px;
  }
  .card {
    position: absolute; left: 310px; width: 580px; height: 331px;
    border-radius: 18px; overflow: hidden;
  }
  .card-back { top: 70px; background: var(--card-black); }
  .card-front { top: 451px; background: var(--card-white); }

  .wordmark {
    position: absolute; text-align: center;
    font-weight: 800; letter-spacing: 0.02em; line-height: 1.05;
    display: flex; flex-direction: column; align-items: center; gap: 10px;
  }
  .wordmark-square {
    width: 34px; height: 34px; background: var(--brand-green);
  }
  .wordmark-name { font-size: 46px; }
  .wordmark-tag { font-size: 17px; letter-spacing: 0.32em; }
  .card-back .wordmark {
    left: 0; right: 0; top: 88px; color: var(--text-light);
  }
  .card-front .wordmark {
    right: 34px; top: 92px; width: 300px; color: var(--text-dark);
  }
  .card-front .wordmark-name { font-size: 34px; }
  .card-front .wordmark-tag { font-size: 13px; }
  .card-front .wordmark-square { width: 26px; height: 26px; }

  .wave { position: absolute; inset: 0; width: 580px; height: 331px; }

  .name-block {
    position: absolute; left: 26px; top: 24px;
    border-left: 10px solid var(--brand-green); padding-left: 14px;
  }
  .person-name {
    font-weight: 800; font-size: 28px; color: var(--brand-green);
    letter-spacing: 0.03em; line-height: 1.1;
  }
  .person-title {
    font-weight: 500; font-size: 13px; color: var(--text-muted);
    letter-spacing: 0.04em; margin-top: 4px;
  }

  .contact {
    position: absolute; left: 30px; top: 168px;
    color: var(--text-light); font-size: 15px; line-height: 1.55;
    list-style: none;
  }
  .contact-address { margin-bottom: 6px; }
  .contact li { display: flex; align-items: center; gap: 10px; }
  .contact svg { width: 14px; height: 14px; flex: none; fill: var(--brand-green); }
</style>
</head>
<body>
<main class="canvas">

  <section class="card card-back" aria-label="Card back">
    <div class="wordmark">
      <span class="wordmark-square"></span>
      <span class="wordmark-name">RIDGEWAY</span>
      <span class="wordmark-tag">DESIGN + BUILD</span>
    </div>
  </section>

  <section class="card card-front" aria-label="Card front">
    <svg class="wave" viewBox="0 0 580 331" aria-hidden="true">
      <path fill="var(--brand-green)" d="M0,132 C130,120 218,152 280,238 C320,292 385,298 580,274 L580,284 C380,308 312,298 268,244 C208,166 128,142 0,146 Z"/>
      <path fill="var(--card-black)" d="M0,152 C120,146 200,172 258,250 C300,306 370,316 580,296 L580,331 L0,331 Z"/>
      <path fill="var(--brand-green)" d="M400,313 C470,312 530,306 580,300 L580,318 C530,322 470,322 400,320 Z"/>
    </svg>

    <div class="name-block">
      <h1 class="person-name">MARCUS HALE</h1>
      <p class="person-title">OWNER-CEO</p>
    </div>

    <ul class="contact">
      <li class="contact-address">Your address, City<br>State, Zip 1234</li>
      <li><svg viewBox="0 0 16 16"><path d="M3 1h3l1.5 4-2 1.2a9 9 0 0 0 4.3 4.3L11 8.5l4 1.5v3a2 2 0 0 1-2 2A12 12 0 0 1 1 3a2 2 0 0 1 2-2z"/></svg>123 456 789</li>
      <li><svg viewBox="0 0 16 16"><path d="M4 0h8a1 1 0 0 1 1 1v14a1 1 0 0 1-1 1H4a1 1 0 0 1-1-1V1a1 1 0 0 1 1-1zm1 2v10h6V2zm3 11a1 1 0 1 0 0 2 1 1 0 0 0 0-2z"/></svg>123 456 789</li>
      <li><svg viewBox="0 0 16 16"><path d="M1 3h14v10H1zm1.5 1.5v.3L8 9l5.5-4.2v-.3zm0 2.2v4.8h11V6.7L8 11z"/></svg>info@ridgewaybuild.com</li>
      <li><svg viewBox="0 0 16 16"><circle cx="8" cy="8" r="7"/></svg>www.ridgewaybuild.com</li>
    </ul>

    <div class="wordmark">
      <span class="wordmark-square"></span>
      <span class="wordmark-name">RIDGEWAY</span>
      <span class="wordmark-tag">DESIGN + BUILD</span>
    </div>
  </section>

</main>
</body>
</html>
```